New Bicycle shop business card

Hi!
I'm looking for a business card for my new proffesional bike mechanics shop. This shop is only for fixing broken bikes and not selling bikes.
Peferbly a modern and sleek and modern design.
Colors: black, grey, red, white
Information:
Name: Rijwielwerkplaats Vanhoutte
Shop owner: Bart Vanhoutte & Marieke Segers
Website: www.rijwielwerkplaats-vanhoutte.be
Email: info@rijwielwerkplaats-vanhoutte.be
Phone number: +32471902368
Street adres: Kerkweg 46
9940 Bellebeke
Slogan/shop information: Herstellingen van alle merken.
Logo: see files.
Target Market(s)
People who seek a mechanic to fix or upgrade their bikes.
Contact Information for Business Card
Information:
Website: info@rijwielwerkplaats-vanhoutte.be
9940 Bellebeke
Logo: see files.

```html
<!DOCTYPE html>
<html lang="nl">
<head>
<meta charset="utf-8">
<title>Rijwielwerkplaats Vanhoutte – Visitekaartje</title>
<link rel="stylesheet" href="https://fonts.googleapis.com/css2?family=Lato:wght@400;700;900&display=swap">
<style>
  :root {
    --backdrop: #e6e3df;
    --card-red: #e0133f;
    --card-black: #1e1e1e;
    --ink-white: #ffffff;
    --rule-white: rgba(255, 255, 255, 0.9);
    --shadow: rgba(0, 0, 0, 0.35);
  }
  * { box-sizing: border-box; margin: 0; padding: 0; }
  html, body {
    width: 1200px;
    height: 900px;
    overflow: hidden;
  }
  body {
    position: relative;
    background: var(--backdrop);
    font-family: "Lato", sans-serif;
    color: var(--ink-white);
  }
  .card {
    position: absolute;
    left: 330px;
    width: 556px;
    height: 343px;
    box-shadow: 3px 4px 8px var(--shadow);
    display: flex;
    flex-direction: column;
    align-items: center;
    text-align: center;
  }
  /* Contact side */
  .card--contact {
    top: 90px;
    background: var(--card-red);
    padding-top: 84px;
  }
  .owners {
    font-weight: 700;
    font-size: 19px;
    letter-spacing: 0.1px;
    line-height: 1.1;
  }
  .role {
    font-size: 15px;
    line-height: 1.2;
  }
  .divider {
    width: 168px;
    height: 1px;
    background: var(--rule-white);
    margin: 9px 0 12px;
  }
  .contact-list {
    list-style: none;
    font-size: 15px;
    line-height: 20px;
  }
  .divider--lower { margin: 9px 0 15px; }
  .address { font-size: 15px; }

  /* Brand side */
  .card--brand {
    top: 470px;
    width: 560px;
    height: 342px;
    background: var(--card-black);
    padding-top: 92px;
  }
  .brand-mark {
    width: 52px;
    height: 52px;
    background: var(--card-red);
    margin-bottom: 36px;
  }
  .brand-name {
    font-weight: 900;
    font-size: 27px;
    letter-spacing: 2px;
    line-height: 1.15;
    text-transform: uppercase;
    color: var(--ink-white);
  }
  .tagline {
    margin-top: 30px;
    font-weight: 700;
    font-size: 14px;
    letter-spacing: 0.3px;
    text-transform: uppercase;
  }
</style>
</head>
<body>
  <section class="card card--contact" aria-label="Contactzijde">
    <h1 class="owners">BART VANHOUTTE &amp; MARIEKE SEGERS</h1>
    <p class="role">Owner</p>
    <div class="divider"></div>
    <ul class="contact-list">
      <li>+32471902368</li>
      <li>info@rijwielwerkplaats-vanhoutte.be</li>
      <li>www.rijwielwerkplaats-vanhoutte.be</li>
    </ul>
    <div class="divider divider--lower"></div>
    <p class="address">Kerkweg 46 9940 Bellebeke</p>
  </section>

  <section class="card card--brand" aria-label="Merkzijde">
    <div class="brand-mark"></div>
    <h2 class="brand-name">Rijwielwerkplaats<br>Vanhoutte</h2>
    <p class="tagline">Herstellingen van alle merken</p>
  </section>
</body>
</html>
```